Card Design for my dog training business Brightpaw Obedience

Need a business card design for my dog training business with my new logo. Want the card to come off professional yet fun. Want it to be very eye catchy as well. I normally have these at vet clinics, pet stores, and groomers. so need it to look better than my competitors.
Target Market(s)
dog owners
Industry/Entity Type
Dog Training
Contact Information for Business Card
needs logo, my name and info
Font styles to use
Serif
Colors
0255a3
ffffff
ec1f27
000000
333333
fbfbfb
Requirements
Must have
- Brightpaw Obedience
- Felix Orland
- 415 903 2276
- info@brightpawobedience.example
- www.brightpawobedience.example

```html
<!DOCTYPE html>
<html lang="en">
<head>
<meta charset="utf-8">
<title>Brightpaw Obedience – Business Card</title>
<link rel="stylesheet" href="https://fonts.googleapis.com/css2?family=Tinos&family=Lato&family=EB+Garamond:ital@1&display=swap">
<style>
  :root {
    --backdrop: #8a8a8a;
    --card-white: #ffffff;
    --card-black: #141414;
    --ink: #000000;
    --ink-soft: #333333;
    --brand-red: #ec1f27;
    --mark-grey: #c4c4c4;
  }
  * { box-sizing: border-box; margin: 0; padding: 0; }
  html, body { width: 1200px; height: 1200px; overflow: hidden; }
  body { background: var(--backdrop); position: relative; }

  .card {
    position: absolute;
    top: 310px;
    height: 594px;
    box-shadow: 2px 3px 6px rgba(0,0,0,.35);
  }
  .card--front { left: 234px; width: 364px; background: var(--card-white); }
  .card--back  { left: 627px; width: 369px; background: var(--card-black); }

  .brand-name {
    position: absolute;
    left: 0; right: 0;
    text-align: center;
    font-family: "Tinos", "Times New Roman", serif;
    font-weight: 400;
    font-size: 34px;
    line-height: 1.15;
    letter-spacing: 1px;
  }
  .card--front .brand-name { top: 210px; color: var(--ink); }
  .card--back  .brand-name { top: 232px; color: var(--mark-grey); }
  .brand-dot {
    position: absolute;
    left: 50%;
    width: 26px; height: 26px;
    margin-left: -13px;
    border-radius: 50%;
  }
  .card--front .brand-dot { top: 165px; background: var(--brand-red); }
  .card--back  .brand-dot { top: 187px; background: var(--mark-grey); }

  .holder-name {
    position: absolute;
    top: 405px; left: 0; right: 0;
    text-align: center;
    font-family: "Tinos", "Times New Roman", serif;
    font-size: 22px;
    color: var(--brand-red);
    letter-spacing: .3px;
  }
  .contact-icons {
    position: absolute;
    top: 447px; left: 87px;
  }
  .contact-list {
    position: absolute;
    top: 484px; left: 0; right: 0;
    text-align: center;
    list-style: none;
    font-family: "Lato", Arial, sans-serif;
    font-size: 17px;
    line-height: 22px;
    color: var(--ink);
  }

  .tagline-band {
    position: absolute;
    top: 452px; left: 0; right: 0;
    height: 45px;
    background: var(--brand-red);
    display: flex; align-items: center; justify-content: center;
    font-family: "EB Garamond", Georgia, serif;
    font-style: italic;
    font-size: 20px;
    color: #ffffff;
  }
  .back-web {
    position: absolute;
    top: 535px; left: 0; right: 0;
    text-align: center;
    font-family: "Tinos", "Times New Roman", serif;
    font-size: 15px;
    letter-spacing: 1.6px;
    color: var(--brand-red);
  }
</style>
</head>
<body>

<section class="card card--front">
  <span class="brand-dot"></span>
  <h1 class="brand-name">Brightpaw<br>Obedience</h1>
  <p class="holder-name">FELIX ORLAND</p>
  <svg class="contact-icons" width="190" height="26" viewBox="0 0 190 26" aria-hidden="true">
    <line x1="0" y1="13" x2="52" y2="13" stroke="#333" stroke-width="1.2"/>
    <line x1="138" y1="13" x2="190" y2="13" stroke="#333" stroke-width="1.2"/>
    <circle cx="67" cy="13" r="12" fill="#ec1f27"/>
    <circle cx="95" cy="13" r="12" fill="#ec1f27"/>
    <circle cx="123" cy="13" r="12" fill="#ec1f27"/>
    <path d="M61 9 q6 -4 12 0 l-1 3 h-2 l-1 -2 h-4 l-1 2 h-2 z M62 14 h10 v4 h-10 z" fill="#fff"/>
    <rect x="88" y="8" width="14" height="10" fill="#fff"/>
    <path d="M88 8 l7 6 l7 -6" fill="none" stroke="#ec1f27" stroke-width="1.2"/>
    <circle cx="123" cy="13" r="6" fill="none" stroke="#fff" stroke-width="1.5"/>
    <path d="M117 13 h12 M123 7 v12" stroke="#fff" stroke-width="1.2"/>
  </svg>
  <ul class="contact-list">
    <li>415 903 2276</li>
    <li>info@brightpawobedience.example</li>
    <li>www.brightpawobedience.example</li>
  </ul>
</section>

<section class="card card--back">
  <span class="brand-dot"></span>
  <p class="brand-name">Brightpaw<br>Obedience</p>
  <p class="tagline-band">“Good manners start with one happy walk a day.”</p>
  <p class="back-web">www.brightpawobedience.example</p>
</section>

</body>
</html>
```